Business Card Design

We provide services doing multiple jobs in the construction industry.Please note: The company name needs to be ROCK SOLID BUILDING SERVICESAttached logo was an example of what we wanted. Can you change up the colors?

Industry/Entity Type

Construction

Contact Information for Business Card

ROCK SOLID BUILDING SERVICES5401 HUDSON BEND RDAUSTIN, TX 78734(512)243-6854ROCKSOLIDBUILDINGSERVICES@GMAIL.COM

```html
<!DOCTYPE html>
<html lang="en">
<head>
<meta charset="utf-8">
<title>Pearlwood Framing Works – Business Card</title>
<link rel="stylesheet" href="https://fonts.googleapis.com/css2?family=Cabin:wght@500;600;700&display=swap">
<style>
  :root {
    --navy: #14174a;
    --sky: #0a9ac9;
    --card: #ffffff;
    --backdrop: #eceef1;
    --ink: #1b1e57;
  }
  * { box-sizing: border-box; margin: 0; padding: 0; }
  html, body {
    width: 1200px; height: 864px; overflow: hidden;
    background: var(--backdrop);
    font-family: "Cabin", sans-serif;
    color: var(--ink);
  }
  .business-card {
    position: absolute; left: 75px; top: 132px;
    width: 1050px; height: 600px;
    background: var(--card);
    box-shadow: 0 6px 24px rgba(20, 23, 74, 0.12);
    overflow: hidden;
  }
  .edge-band {
    position: absolute; left: 0; top: 0; width: 46px; height: 100%;
    background: linear-gradient(to bottom, var(--navy) 0 70%, var(--sky) 70% 100%);
  }
  .company-name {
    position: absolute; left: 125px; top: 82px;
    font-weight: 700; line-height: 1.1;
  }
  .company-name .primary { display: block; font-size: 56px; letter-spacing: 1px; }
  .company-name .secondary { display: block; font-size: 36px; letter-spacing: 0.5px; margin-top: 8px; }
  .brand-mark {
    position: absolute; left: 640px; top: 88px;
    display: flex; align-items: center; gap: 18px;
  }
  .brand-mark .mark-square { width: 54px; height: 54px; background: var(--navy); }
  .brand-mark .mark-name {
    font-weight: 700; font-size: 34px; line-height: 1.1; color: var(--navy);
  }
  .contact-list {
    position: absolute; left: 125px; top: 418px;
    list-style: none; font-weight: 600; font-size: 28px; line-height: 1.35;
  }
  .contact-list li { display: flex; align-items: center; gap: 22px; }
  .contact-list svg { width: 26px; height: 26px; flex: none; }
</style>
</head>
<body>
  <div class="business-card">
    <div class="edge-band"></div>

    <h1 class="company-name">
      <span class="primary">PEARLWOOD</span>
      <span class="secondary">FRAMING WORKS</span>
    </h1>

    <div class="brand-mark">
      <span class="mark-square"></span>
      <span class="mark-name">PEARLWOOD<br>FRAMING WORKS</span>
    </div>

    <ul class="contact-list">
      <li>
        <svg viewBox="0 0 24 24" aria-hidden="true"><rect x="6" y="2" width="12" height="20" rx="2.5" fill="none" stroke="var(--sky)" stroke-width="2.4"/><circle cx="12" cy="18.5" r="1.2" fill="var(--sky)"/></svg>
        <span>(512)555-0193</span>
      </li>
      <li>
        <svg viewBox="0 0 24 24" aria-hidden="true"><rect x="2" y="5" width="20" height="14" fill="var(--sky)"/><path d="M2 5l10 8 10-8M2 19l7-6M22 19l-7-6" fill="none" stroke="#fff" stroke-width="1.6"/></svg>
        <span>Pearlwoodframingworks@mailnest.example</span>
      </li>
      <li><span>7732 Fernglen Pass LN Austin, TX 78734</span></li>
    </ul>
  </div>
</body>
</html>
```